Prepared Meal Company Needs Menu Design

We are a pre-prepared meal delivery company called Grubb Larder.

We have a menu in excel but needs to be designed to look good and appealing to customers. The menu should be clean, easy to ready, and show:Title (Pupusa)Tags (V, V+, GF - Use a cool vegan logo for the V+ and logo for vegetarian V symbol)Price (12.99)DescriptionBrand colors are orange white and green. Design is clean, crisp and can incorporate natural elements like leaf shaped symbols, etc. Screenshots from our website attached for inspiration.

Target Market(s)

Broad demographics

Industry/Entity Type

Restaurant

Font styles to use
Sans Serif

Requirements
Must have
• The menu design should be commensurate with the website under development
• https://grubblarder.dishboard.example
Nice to have
• Should have appropriate graphics
Should not have
• Modifiers do not need to be shown (these are shown in the excel only).

```html
<!DOCTYPE html>
<html lang="en">
<head>
<meta charset="utf-8">
<title>Grubb Larder Menu</title>
<link href="https://fonts.googleapis.com/css2?family=Oswald:wght@400;500&family=Dancing+Script:wght@400;700&display=swap" rel="stylesheet">
<style>
:root{
  --backdrop:#333333;
  --paper:#fafafa;
  --ribbon:#f06a22;
  --ribbon-text:#ffffff;
  --title-green:#2f8a34;
  --ink:#1f1f1f;
  --leaf-light:#b9dca0;
  --leaf-mid:#8cc58a;
  --leaf-deep:#6fae7a;
}
*{margin:0;padding:0;box-sizing:border-box}
html,body{width:1200px;height:1200px;overflow:hidden;background:var(--backdrop)}
.menu-page{position:absolute;left:195px;top:25px;width:812px;height:1150px;background:var(--paper);overflow:hidden}
.leaf-art{position:absolute;opacity:.55}
.leaf-top{left:215px;top:-20px;width:360px;height:310px;border-radius:0 0 50% 50%;background:radial-gradient(ellipse at 50% 30%,var(--leaf-mid),rgba(185,220,160,0) 70%)}
.leaf-right{right:-40px;top:230px;width:160px;height:520px;border-radius:50%;background:radial-gradient(ellipse,var(--leaf-light),rgba(185,220,160,0) 70%)}
.leaf-bottom{left:230px;top:780px;width:600px;height:420px;border-radius:50% 50% 0 0;background:radial-gradient(ellipse at 50% 70%,var(--leaf-deep),rgba(111,174,122,0) 70%)}
.leaf-left{left:-30px;top:300px;width:120px;height:400px;border-radius:50%;background:radial-gradient(ellipse,var(--leaf-light),rgba(185,220,160,0) 70%)}
.section{position:absolute}
.ribbon{height:56px;background:var(--ribbon);color:var(--ribbon-text);font-family:'Oswald',sans-serif;font-weight:400;font-size:22px;white-space:nowrap;display:flex;align-items:center;justify-content:center;letter-spacing:0;clip-path:polygon(0 0,100% 0,96.5% 50%,100% 100%,0 100%,3.5% 50%)}
.ribbon.long{font-size:20px}
.items{position:absolute}
.item{margin-bottom:2px}
.item-name,.item-head{font-family:'Dancing Script',cursive;font-weight:700;font-size:16px;color:var(--title-green);line-height:20.5px}
.item-head{display:flex;align-items:baseline;white-space:nowrap}
.item-head .leader{flex:1;border-bottom:1.5px dotted var(--title-green);margin:0 4px;transform:translateY(-4px)}
.item-head .price{font-size:16px}
.item-desc{font-family:'Dancing Script',cursive;font-weight:400;font-size:15px;color:var(--ink);line-height:20.5px;max-width:350px}
</style>
</head>
<body>
<main class="menu-page">
  <div class="leaf-art leaf-top" role="img" aria-label="Hanging green leaf and asparagus illustration"></div>
  <div class="leaf-art leaf-right" role="img" aria-label="Green leafy greens illustration"></div>
  <div class="leaf-art leaf-left" role="img" aria-label="Green leaf illustration"></div>
  <div class="leaf-art leaf-bottom" role="img" aria-label="Leafy greens and asparagus bunch illustration"></div>

  <section class="section breakfast" style="left:17px;top:68px;width:367px">
    <div class="ribbon long">BREAKFAST - ALL MENU ITEMS SOY FREE</div>
  </section>
  <div class="items" style="left:12px;width:380px;top:132px">
    <div class="item"><div class="item-head"><span>Cinnamon-Apple Sunrise Oats</span><span class="leader"></span><span class="price">6.99$</span></div><div class="item-desc">Almond Milk &amp; Ceylon Cinnamon, Marinated Golden Raisins, Macca Powder, Apple-Pecan Crumble</div></div>
    <div class="item"><div class="item-head"><span>Acai Yogurt (V, GF)</span><span class="leader"></span><span class="price">7.99$</span></div><div class="item-desc">Coconut, Goji, Seasonal Fruit, Crunchy Chia Seeds, Ceylon Cinnamon</div></div>
    <div class="item"><div class="item-head"><span>Harvest Sprout Cereal &amp; Yogurt (V)</span><span class="leader"></span><span class="price">7.49$</span></div><div class="item-desc">Apricot-Pear Compote, Almond &amp; Saba Drizzle</div></div>
    <div class="item"><div class="item-head"><span>St. Benedict's Eggs (V, Dairy Free)</span><span class="leader"></span><span class="price">9.49$</span></div><div class="item-desc">2 Soft Yolk Eggs over Rosemary Polenta, Caramelized Onion, Mushrooms &amp; Asparagus, Lemon</div></div>
    <div class="item"><div class="item-name">Pomegranate &amp; Saffron</div><div class="item-head"><span>Shakshuka (V, GF, Dairy Free)</span><span class="leader"></span><span class="price">9.49$</span></div><div class="item-desc" style="max-width:375px">2 Soft Yolk Eggs over Roasted Tomatoes, Onions &amp; Peppers, Garden Herb Oil, Rosemary, Oregano &amp; Thyme with Handmade Gluten-Free Flatbread</div></div>
    <div class="item"><div class="item-head"><span>Sweet Potato Hash (V+, GF)</span><span class="leader"></span><span class="price">8.99$</span></div><div class="item-desc">Broccolini, Cherry Tomato, Asparagus, Roasted Peppers &amp; Onions, Rosemary-Nutritional Yeast</div></div>
    <div class="item"><div class="item-head"><span>Mom's Frittata (V, GF)</span><span class="leader"></span><span class="price">11.99$</span></div><div class="item-desc">Roasted Cherry Tomato, Goat Cheese &amp; Baby Spinach with Sweet Potato Homefries</div></div>
    <div class="item"><div class="item-head"><span>Country Style Breakfast Sandwich (V)</span><span class="leader"></span><span class="price">13.99$</span></div><div class="item-desc">Arugula, Goat Cheese, Cherry Tomatoes &amp; Lemon with Mom's Frittata on Harvest Sprout Bread</div></div>
  </div>

  <section class="section appetizers" style="left:425px;top:68px;width:368px">
    <div class="ribbon">APPETIZERS</div>
  </section>
  <div class="items" style="left:420px;width:378px;top:137px">
    <div class="item"><div class="item-name">Avocado Super-Toast (V+) [GF with Flatbread] NEED</div><div class="item-head"><span>PHOTO WITHOUT FISH</span><span class="leader"></span><span class="price">9.49$</span></div><div class="item-desc">Shaved Fennel &amp; Golden Beets, Avocado, Garden Herb Oil, Lemon Juice, Ground Flax, Hemp Seed, Golden Raisin &amp; Moringa on Harvest Sprout Whole Wheat Bread</div></div>
    <div class="item"><div class="item-head"><span>Pupusa (V, GF) NEED PHOTO WITHOUT MEAT</span><span class="leader"></span><span class="price">9.49$</span></div><div class="item-desc">Arugula, Goat Cheese, Cherry Tomatoes &amp; Lemon with Mom's Fritatta on Harvest Sprout Bread</div></div>
    <div class="item"><div class="item-head"><span>Pupusa Deluxe (GF)</span><span class="leader"></span><span class="price">13.9$</span></div><div class="item-desc">Sous Vide Bison Shortrib, Goat Cheese, Ayocote &amp; Avocado Puree, Nopales, Cilantro-Lime Yogurt, Inca Corn Crumble, Tropical Acai Hot Sauce</div></div>
    <div class="item"><div class="item-head"><span>Egyptian Flatbread (V, GF)</span><span class="leader"></span><span class="price">11.99$</span></div><div class="item-desc">Honey-Chamomile Yogurt, Braised Cherry Tomatoes, Sumac &amp; Pistachio Dukkha, Garlic &amp; Micro Radish on Handmade Gluten-Free Flatbread</div></div>
    <div class="item"><div class="item-head"><span>Green Street Tacos (V+, GF)</span><span class="leader"></span><span class="price">9.99$</span></div><div class="item-desc">Sugar Snap Peas, Guacamole, Radish &amp; Inca Corn Crumble on 2 Handmade Corn Tortillas.</div></div>
    <div class="item"><div class="item-head"><span>Marinated Squash Tacos (V+, GF)</span><span class="leader"></span><span class="price">9.99$</span></div><div class="item-desc">Chayote Escabeche, Jalapeno, Guacamole, Carrots, Radish, Pepitas &amp; Cilantro, on 2 Handmade Corn Tortillas.</div></div>
    <div class="item"><div class="item-head"><span>Soft Yolk Egg &amp; Avocado "Toast" Flatbread (V, GF)</span><span class="leader"></span><span class="price">9.99$</span></div><div class="item-desc">Ayocote &amp; Avocado Puree, Guacamole, Sunflower Seeds, Inca Corn, Arugula, Lime &amp; Soft Yolk Egg on Handmade Gluten-Free Flatbread</div></div>
  </div>

  <section class="section salad" style="left:17px;top:680px;width:367px">
    <div class="ribbon">SALAD</div>
  </section>
  <div class="items" style="left:12px;width:380px;top:748px">
    <div class="item"><div class="item-name">Larder Salad (V, GF, Dairy Free)</div><div class="item-head"><span>[V+ if No Cider Vinaigrette]</span><span class="leader"></span><span class="price">9.99$</span></div><div class="item-desc" style="max-width:275px">Baby Spinach &amp; Arugula, Chilled Sorghum, Cranberry, Pistachio, Apple Cider Vinaigrette, Butternut Squash &amp; Sunflower Seeds</div></div>
    <div class="item"><div class="item-head"><span>Vegan Chef's Salad (V+, GF)</span><span class="leader"></span><span class="price">9.99$</span></div><div class="item-desc" style="max-width:335px">Arugula, Spinach &amp; Avocado, Pistachio, Saba, Roasted Potatoes &amp; Carrots</div></div>
    <div class="item"><div class="item-name">Beach Day Greens (V, GF)</div><div class="item-head"><span>[V+ if No Cider Vinaigrette &amp; Goat Cheese]</span><span class="leader"></span><span class="price">9.99$</span></div><div class="item-desc" style="max-width:320px">Baby Lettuces &amp; Avocado, Asparagus, Strawberries, Basil &amp; Goat Cheese with Cider Vinaigrette</div></div>
    <div class="item"><div class="item-name">Emporer's Greens (V, GF)</div><div class="item-head"><span>[V+ if No Carrot-Ginger Vinaigrette]</span><span class="leader"></span><span class="price">9.99$</span></div><div class="item-desc" style="max-width:320px">Baby Lettuces &amp; Avocado, Asparagus, Strawberries, Basil &amp; Goat Cheese with Cider Vinaigrette</div></div>
  </div>

  <section class="section soups" style="left:427px;top:700px;width:368px">
    <div class="ribbon">SOUPS</div>
  </section>
  <div class="items" style="left:423px;width:377px;top:766px">
    <div class="item"><div class="item-name">Seasonal Vegetable Minestrone with Free Range Turkey</div><div class="item-head"><span>Meatballs (GF)</span><span class="leader"></span><span class="price">9.49$</span></div><div class="item-desc">Ayocote Beans, Roasted Tomatoes, Carrots, Onions &amp; Bell Pepper, Snap Peas, Garnett Yam, Rosemary &amp; Oregano</div></div>
    <div class="item"><div class="item-head"><span>Sweet Carrot &amp; Coriander Soup (V+, GF)</span><span class="leader"></span><span class="price">5.99$</span></div><div class="item-desc">Garden Herb Oil, Cilantro, Toasted Pepita</div></div>
    <div class="item"><div class="item-name">Butternut Squash &amp; Nopale Chili (V, GF)</div><div class="item-head"><span>[V+ if No Goat Cheese]</span><span class="leader"></span><span class="price">9.49$</span></div><div class="item-desc" style="max-width:320px">Vegan Brown Butter Sage &amp; Pepita Crumble, Tomato, Goat Cheese, Ayocote Beans &amp; Ancho Chile</div></div>
    <div class="item"><div class="item-head"><span>Rowan's Chicken Soup (GF, Dairy Free)</span><span class="leader"></span><span class="price">9.49$</span></div><div class="item-desc" style="max-width:335px">Gluten-Free Sorghum Penne, Root Vegetables, Oregano &amp; Peppercorns on the Vine</div></div>
  </div>
</main>
</body>
</html>
```